Frostvale Harborline LLC

we need a business card design

Industry/Entity Type

hvac

Contact Information for Business Card

my logo

Requirements
Must have
• my logo and same colors

```html
<!DOCTYPE html>
<html lang="en">
<head>
<meta charset="utf-8">
<title>Frostvale Harborline LLC – Business Card</title>
<link href="https://fonts.googleapis.com/css2?family=Montserrat:wght@400;700&display=swap" rel="stylesheet">
<style>
  :root {
    --backdrop: #222222;
    --brand-blue: #0062aa;
    --sky-blue: #0aafe0;
    --sun-gold: #f5b752;
    --paper: #ffffff;
  }
  * { box-sizing: border-box; margin: 0; padding: 0; }
  html, body {
    width: 1093px;
    height: 1200px;
    overflow: hidden;
    background: var(--backdrop);
    font-family: "Montserrat", Arial, sans-serif;
  }
  .card {
    position: absolute;
    left: 265px;
    width: 596px;
    height: 363px;
    border-radius: 18px;
    overflow: hidden;
  }
  .card--front { top: 225px; background: var(--paper); }
  .card--back  { top: 616px; height: 366px; background: var(--brand-blue); }

  .front-waves {
    position: absolute;
    inset: 0;
    width: 100%;
    height: 100%;
  }

  .wordmark {
    position: absolute;
    font-weight: 700;
    text-align: center;
    line-height: 1.15;
  }
  .card--front .wordmark {
    left: 330px;
    top: 72px;
    width: 240px;
    font-size: 24px;
    color: var(--brand-blue);
  }
  .card--back .wordmark {
    left: 0;
    top: 138px;
    width: 100%;
    font-size: 40px;
    color: var(--paper);
  }

  .contact-block {
    position: absolute;
    left: 15px;
    top: 188px;
    color: var(--paper);
  }
  .contact-name {
    font-size: 24px;
    font-weight: 700;
    color: var(--sun-gold);
    line-height: 1.1;
  }
  .contact-role {
    font-size: 14px;
    margin-top: 3px;
  }
  .contact-address {
    font-size: 14px;
    line-height: 17px;
    margin-top: 10px;
    padding-left: 2px;
  }
  .contact-lines {
    list-style: none;
    margin-top: 8px;
  }
  .contact-lines li {
    display: flex;
    align-items: center;
    font-size: 14.5px;
    height: 21px;
  }
  .contact-icon {
    width: 14px;
    height: 14px;
    margin: 0 10px 0 2px;
    flex-shrink: 0;
  }
</style>
</head>
<body>

<section class="card card--front" aria-label="Business card front">
  <svg class="front-waves" viewBox="0 0 1001 610" preserveAspectRatio="none" aria-hidden="true">
    <path fill="var(--sun-gold)" d="M0,240 C120,178 270,180 430,255 C570,322 650,398 760,396 C880,394 960,300 1001,240 L1001,610 L0,610 Z"/>
    <path fill="var(--paper)" d="M0,246 C140,196 290,200 430,280 C570,365 655,452 760,456 C880,460 955,380 1001,325 L1001,610 L0,610 Z"/>
    <path fill="var(--sky-blue)" d="M0,255 C140,205 290,212 425,288 C565,372 655,478 760,484 C870,490 940,420 980,362 L1001,610 L0,610 Z"/>
    <path fill="var(--paper)" d="M0,275 C150,215 300,232 430,310 C565,400 660,500 760,500 C875,500 950,420 985,375 L1001,610 L0,610 Z"/>
    <path fill="var(--brand-blue)" d="M0,287 C150,222 300,245 430,322 C565,412 660,512 765,512 C880,512 960,430 1001,380 L1001,610 L0,610 Z"/>
  </svg>

  <div class="wordmark">Frostvale<br>Harborline LLC</div>

  <div class="contact-block">
    <h1 class="contact-name">Dana Whitcombe</h1>
    <p class="contact-role">Managing Director</p>
    <p class="contact-address">48 Orchard Lane,<br>Brookmere, NY 12045</p>
    <ul class="contact-lines">
      <li>
        <svg class="contact-icon" viewBox="0 0 14 14" aria-hidden="true">
          <rect x="3" y="0.5" width="8" height="13" rx="1.5" fill="none" stroke="var(--sun-gold)" stroke-width="1.6"/>
          <circle cx="7" cy="11.3" r="0.8" fill="var(--sun-gold)"/>
        </svg>
        +1 (555) 014-2290
      </li>
      <li>
        <svg class="contact-icon" viewBox="0 0 14 14" aria-hidden="true">
          <rect x="0.5" y="3" width="13" height="9" rx="1" fill="var(--sun-gold)"/>
          <path d="M0.8,3.5 L7,8 L13.2,3.5" fill="none" stroke="var(--brand-blue)" stroke-width="1"/>
        </svg>
        hello@frostvaleharbor.com
      </li>
      <li>
        <svg class="contact-icon" viewBox="0 0 14 14" aria-hidden="true">
          <circle cx="7" cy="7" r="6.3" fill="var(--sun-gold)"/>
          <ellipse cx="7" cy="7" rx="2.6" ry="6.3" fill="none" stroke="var(--brand-blue)" stroke-width="0.9"/>
          <path d="M0.8,7 H13.2" stroke="var(--brand-blue)" stroke-width="0.9"/>
        </svg>
        www.frostvaleharbor.com
      </li>
    </ul>
  </div>
</section>

<section class="card card--back" aria-label="Business card back">
  <div class="wordmark">Frostvale<br>Harborline LLC</div>
</section>

</body>
</html>
```